Oil and Gas Exploration and Production company needs a business card design

We need a business card design using our logo and colors in the logo. We want a mainstream design.

```html
<!DOCTYPE html>
<html lang="en">
<head>
<meta charset="utf-8">
<title>Corvan Oil &amp; Gas – Business Card</title>
<link rel="stylesheet" href="https://fonts.googleapis.com/css2?family=Roboto+Slab:wght@400;700;800&display=swap">
<style>
  :root {
    --backdrop: #7d6043;
    --card: #fbfbfa;
    --ink: #111111;
    --gold: #d4a233;
    --muted: #3a3a3a;
    --rule: #cfcfcf;
  }
  * { box-sizing: border-box; margin: 0; padding: 0; }
  html, body { width: 1200px; height: 911px; overflow: hidden; }
  body {
    background: var(--backdrop);
    font-family: "Roboto Slab", Georgia, serif;
    color: var(--ink);
    position: relative;
  }
  .card {
    position: absolute;
    width: 540px;
    height: 320px;
    background: var(--card);
    border-radius: 20px;
    overflow: hidden;
    box-shadow: 0 10px 24px rgba(0,0,0,.35);
  }
  .card--contact { left: 70px; top: 120px; }
  .card--brand { left: 590px; top: 470px; }

  /* contact side */
  .emblem-band { position: absolute; left: 0; top: 0; width: 220px; height: 320px; }
  .contact-body {
    position: absolute; left: 245px; top: 34px; right: 30px;
  }
  .person-name { font-size: 21px; font-weight: 800; letter-spacing: 1px; }
  .person-title { font-size: 12px; color: var(--gold); letter-spacing: 1px; margin-top: 4px; }
  .divider { display: flex; align-items: center; gap: 0; margin: 16px 0; }
  .divider::before { content: ""; width: 34px; height: 3px; background: var(--gold); }
  .divider::after { content: ""; flex: 1; height: 1px; background: var(--rule); }
  .address { font-size: 13px; line-height: 1.55; color: var(--muted); }
  .contact-list { list-style: none; font-size: 12px; line-height: 1.75; color: var(--muted); }
  .contact-list li { display: flex; align-items: center; gap: 9px; }
  .contact-list svg { width: 12px; height: 12px; flex: none; }

  /* brand side */
  .brand-lockup {
    position: absolute; left: 0; right: 0; top: 118px;
    display: flex; align-items: center; justify-content: center; gap: 12px;
  }
  .brand-dot { width: 22px; height: 22px; border-radius: 50%; background: var(--gold); }
  .brand-name { font-size: 40px; font-weight: 800; color: var(--ink); letter-spacing: .5px; }
  .brand-web {
    position: absolute; left: 0; right: 0; bottom: 36px;
    text-align: center; font-size: 12px; letter-spacing: 7px; color: var(--muted);
  }
</style>
</head>
<body>

<section class="card card--contact">
  <svg class="emblem-band" viewBox="0 0 220 320" role="img" aria-label="Brand emblem area on black band">
    <path d="M0 0 H120 Q240 160 120 320 H0 Z" fill="#0c0c0c"/>
  </svg>
  <div class="contact-body">
    <h1 class="person-name">DANIEL MARSH</h1>
    <p class="person-title">CEO/FOUNDER</p>
    <div class="divider"></div>
    <p class="address">4120 Birch Hollow Road<br>Fairbanks, Alaska 99701</p>
    <div class="divider"></div>
    <ul class="contact-list">
      <li><svg viewBox="0 0 12 12"><path d="M2 1 L4.5 1 L5.5 3.5 L4 4.7 Q5 7 7.3 8 L8.5 6.5 L11 7.5 L11 10 Q5 11 1 3 Z" fill="#111"/></svg>555 214 0193</li>
      <li><svg viewBox="0 0 12 12"><rect x="3" y="0.5" width="6" height="11" rx="1.2" fill="none" stroke="#111" stroke-width="1.3"/><circle cx="6" cy="9.5" r=".8" fill="#111"/></svg>555 730 4482</li>
      <li><svg viewBox="0 0 12 12"><rect x="1" y="4" width="10" height="6" rx="1" fill="#111"/><rect x="3" y="1" width="6" height="3" fill="none" stroke="#111" stroke-width="1"/></svg>555 861 2207</li>
      <li><svg viewBox="0 0 12 12"><rect x="0.5" y="2" width="11" height="8" rx="1" fill="#111"/><path d="M1 2.5 L6 6.5 L11 2.5" fill="none" stroke="#fff" stroke-width="1"/></svg>info@corvanoilgas.com</li>
      <li><svg viewBox="0 0 12 12"><circle cx="6" cy="6" r="5.3" fill="none" stroke="#111" stroke-width="1.2"/><path d="M0.8 6 H11.2 M6 0.7 Q2.5 6 6 11.3 M6 0.7 Q9.5 6 6 11.3" fill="none" stroke="#111" stroke-width="1"/></svg>www.corvanoilgas.com</li>
    </ul>
  </div>
</section>

<section class="card card--brand">
  <div class="brand-lockup">
    <span class="brand-dot"></span>
    <span class="brand-name">Corvan Oil &amp; Gas</span>
  </div>
  <p class="brand-web">www.corvanoilgas.com</p>
</section>

</body>
</html>
```